Take your idea to next level of implementation

Need a website for the training program that we are launching. Lantern on Hill is training provided to aspiring entrepreneurs.
The training comprises of business skills imparted to participants in order to help them develop their ideas and take the ideas to the next level of implementation.
The training program will be conducted in 8 sessions spanning over 5 months.

Coding

Coded - Design and coding required

Number of Pages Required

1 page

Colors

Designer to choose colors to be used in the design.

Requirements
Must have
• The project must have single page
Nice to have
• It would be nice to have a landing page that feels positive and will attract applicants.
• It should be highly professional.
Should not have
• Pictures used in the template should not have any people.

```html
<!DOCTYPE html>
<html lang="en">
<head>
<meta charset="utf-8">
<title>Lantern on Hill</title>
<link href="https://fonts.googleapis.com/css2?family=Poppins:wght@400;500;600;700&display=swap" rel="stylesheet">
<style>
:root{
  --blue:#3a7fd5;
  --blue-dark:#2f6fc0;
  --orange:#f7931e;
  --ink:#222222;
  --muted:#555555;
  --grey-bg:#f2f2f2;
  --line:#dddddd;
  --footer:#1d1d1d;
  --white:#ffffff;
}
*{margin:0;padding:0;box-sizing:border-box}
html,body{width:1200px;height:5172px;overflow:hidden}
body{font-family:'Poppins',sans-serif;color:var(--ink);background:var(--white);position:relative}
.abs{position:absolute}
.center{text-align:center;left:0;width:1200px}

/* header */
.site-header{position:absolute;top:0;left:0;width:1200px;height:92px;background:var(--white)}
.brand{position:absolute;left:76px;top:24px;display:flex;align-items:center;gap:12px}
.brand-mark{width:40px;height:40px;border-radius:50%;border:3px solid var(--blue)}
.brand-name{font-weight:700;font-size:19px;line-height:19px;color:#1f3b66;width:110px;text-transform:uppercase}
.main-nav{position:absolute;left:362px;top:42px;display:flex;gap:0}
.main-nav a{font-size:13px;font-weight:600;color:#333;text-decoration:none;text-transform:uppercase;margin-right:46px}
.main-nav a.active{color:var(--blue)}

/* hero */
.hero{position:absolute;top:92px;left:0;width:1200px;height:706px;overflow:hidden}
.hero-photo{position:absolute;inset:0;background:linear-gradient(120deg,#4b4f57 0%,#8a8d93 40%,#b8bbc0 60%,#5d6067 100%)}
.hero-photo::after{content:"";position:absolute;inset:0;background:rgba(20,22,28,.35)}
.hero-title{position:absolute;top:222px;left:0;width:1200px;text-align:center;color:var(--white);font-weight:700;font-size:64px;letter-spacing:1px}
.hero-sub{position:absolute;top:300px;left:180px;width:840px;text-align:center;color:var(--white);font-weight:700;font-size:22px;line-height:39px;text-transform:uppercase}
.btn{display:block;position:absolute;background:var(--orange);color:var(--white);font-weight:600;text-align:center;border-radius:30px;text-transform:uppercase;text-decoration:none}
.hero .btn{left:504px;top:412px;width:190px;height:48px;line-height:48px;font-size:17px}
.dots{position:absolute;display:flex;gap:12px}
.dot{width:14px;height:14px;border-radius:50%;background:var(--white)}
.dot.on{background:var(--blue)}
.hero .dots{left:550px;top:577px}
.hero-wave{position:absolute;left:0;bottom:0}

/* about */
.section-title{position:absolute;left:0;width:1200px;text-align:center;font-weight:700;font-size:31px;color:var(--ink);text-transform:uppercase}
.about-lead{position:absolute;left:76px;top:884px;width:1048px;text-align:center;font-size:19px;line-height:39px;text-transform:uppercase;color:#333}
.about-note{position:absolute;left:150px;top:1013px;width:900px;text-align:center;font-size:19px;line-height:30px;color:var(--blue)}
.about-apply{position:absolute;left:0;top:1093px;width:1200px;text-align:center;font-size:15px;line-height:32px;text-transform:uppercase;color:#333}
.about-btn{left:504px;top:1182px;width:190px;height:48px;line-height:48px;font-size:17px}
.about-free{position:absolute;left:0;top:1262px;width:1200px;text-align:center;font-weight:600;font-size:16px;text-transform:uppercase}

/* split rows */
.split{position:absolute;left:0;width:1200px;height:466px}
.split-media{position:absolute;top:0;width:600px;height:466px}
.split-copy{position:absolute;top:0;width:600px;height:466px;background:var(--grey-bg)}
.split-copy h2{font-size:31px;font-weight:700;text-transform:uppercase;color:#333;margin-bottom:20px}
.split-copy p{font-size:15px;line-height:31px;color:#444}
.split-copy p strong{color:var(--blue);font-weight:600}

.programme{top:1352px}
.programme .split-media{left:0;background:linear-gradient(135deg,#c9b89a 0%,#e2d6c3 45%,#8c8a86 70%,#d7cbb7 100%)}
.programme .split-copy{left:600px;padding:56px 130px 0 30px}
.programme .btn{position:static;display:inline-block;margin-top:34px;width:190px;height:48px;line-height:48px;font-size:17px}

.why{top:1818px}
.why .split-copy{left:0;padding:74px 40px 0 76px}
.why .split-media{left:600px;background:linear-gradient(180deg,#eeeeec 0%,#e4e3e0 70%,#b79268 100%)}

/* faq */
.faq-list{position:absolute;left:196px;top:2416px;width:812px}
.faq-open{border-bottom:1px solid var(--line);padding-bottom:24px;margin-bottom:22px}
.faq-q{display:flex;justify-content:space-between;align-items:center;font-size:16px;color:#333;height:58px}
.faq-open .faq-q{height:auto;color:var(--blue);font-weight:600;margin-bottom:22px}
.faq-a{font-size:13px;line-height:27px;color:#444;margin-bottom:14px;width:740px}
.chev{width:14px;height:14px;flex:none}
.faq-btn{position:absolute;left:494px;top:3134px;width:208px;height:52px;line-height:52px;border-radius:30px;background:var(--blue);color:var(--white);font-weight:600;font-size:16px;text-align:center;text-decoration:none}

/* academic */
.academic{top:3352px}
.academic .split-media{left:0;background:linear-gradient(120deg,#f4ecd9 0%,#f9f5ea 45%,#cfc3ad 100%)}
.academic .split-copy{left:600px;padding:54px 90px 0 38px}
.partner-row{display:flex;gap:44px;margin-top:52px;align-items:center}
.partner{display:flex;align-items:center;gap:10px;font-weight:600;font-size:20px;color:#1f4f95}
.partner-dot{width:44px;height:44px;border-radius:50%;background:#1f4f95}

/* people */
.people{position:absolute;top:3818px;left:0;width:1200px;height:620px;background:var(--blue)}
.people h2{position:absolute;top:46px;left:0;width:1200px;text-align:center;color:var(--white);font-size:31px;font-weight:600;text-transform:uppercase}
.people-lead{position:absolute;top:114px;left:0;width:1200px;text-align:center;color:var(--white);font-size:18px}
.card{position:absolute;top:180px;width:242px;height:282px;background:var(--white);border-radius:16px;text-align:center;padding-top:14px}
.avatar{width:144px;height:144px;border-radius:50%;margin:0 auto 16px;background:radial-gradient(circle at 50% 40%,#9a9a9a,#3a3a3a)}
.card h3{font-size:15px;font-weight:500;color:var(--orange);text-transform:uppercase;margin-bottom:6px}
.card p{font-size:12.5px;line-height:20px;color:#333;padding:0 16px}
.people .dots{left:584px;top:521px}
.people .dot.on{background:#222}

/* apply */
.apply{position:absolute;top:4380px;left:0;width:1200px;height:536px;overflow:hidden}
.apply-photo{position:absolute;inset:0;background:linear-gradient(180deg,#8d8d8d 0%,#a09890 50%,#756a63 100%)}
.apply-photo::after{content:"";position:absolute;inset:0;background:rgba(25,25,25,.55)}
.people-wave{position:absolute;top:0;left:0}
.apply h2{position:absolute;top:138px;left:0;width:1200px;text-align:center;color:var(--white);font-size:31px;font-weight:600;text-transform:uppercase}
.apply-lead{position:absolute;top:206px;left:0;width:1200px;text-align:center;color:var(--white);font-size:19px;line-height:37px}
.field{position:absolute;width:332px;height:44px;background:var(--white);border-radius:24px;font-size:15px;color:#444;line-height:44px;padding-left:24px}
.apply .btn{left:494px;top:424px;width:208px;height:56px;line-height:56px;font-size:17px}

/* footer */
.site-footer{position:absolute;top:4916px;left:0;width:1200px;height:98px;background:var(--footer)}
.copyright{position:absolute;left:76px;top:40px;color:#ddd;font-size:12px}
.social{position:absolute;left:938px;top:36px;display:flex;gap:22px;align-items:center}
.social span{width:20px;height:20px;border-radius:50%;background:#eee;display:block}
.social .x10{width:auto;height:auto;background:none;color:#ddd;font-size:12px;border-radius:0;margin-left:24px}
</style>
</head>
<body>

<header class="site-header">
  <div class="brand"><span class="brand-mark"></span><span class="brand-name">Lantern on Hill</span></div>
  <nav class="main-nav">
    <a class="active" href="#">Home</a><a href="#">About</a><a href="#">Programme</a><a href="#">FAQ</a><a href="#">Academic Support</a><a href="#">People</a><a href="#">Contact</a>
  </nav>
</header>

<section class="hero">
  <div class="hero-photo" role="img" aria-label="Office desk with laptop and growth charts"></div>
  <h1 class="hero-title">LANTERN ON HILL</h1>
  <p class="hero-sub">Lantern on Hill lab is a project delivered by Northfield School of Business, in partnership with Castellano University.</p>
  <a class="btn" href="#">Apply Now</a>
  <div class="dots"><span class="dot on"></span><span class="dot"></span><span class="dot"></span><span class="dot"></span></div>
  <svg class="hero-wave" width="1200" height="120" viewBox="0 0 1200 120">
    <path d="M0,20 C300,95 700,100 1200,40 L1200,120 L0,120Z" fill="var(--blue)"/>
    <path d="M0,28 C300,110 700,118 1200,92 L1200,120 L0,120Z" fill="#ffffff"/>
  </svg>
</section>

<h2 class="section-title" style="top:816px">About</h2>
<p class="about-lead">Lantern on Hill lab is a project delivered by Northfield School of Business, in partnership with Castellano University. This project is first of its kind training programme to aspiring entrepreneurs in India.</p>
<p class="about-note">The first round of applications is open till 1 st MARCH, 2020. If you would like to be part of the training and to be informed further please fill in the form below.</p>
<p class="about-apply">To apply for the first edition of this project,<br>please click below and fill in details to express your interest</p>
<a class="btn about-btn" href="#">Apply Now</a>
<p class="about-free">The training is completely free of charge</p>

<section class="split programme">
  <div class="split-media" role="img" aria-label="Top view of a work desk with laptop, notebook, coffee and snacks"></div>
  <div class="split-copy">
    <h2>Programme</h2>
    <p>So, you have an idea?<br>What next?<br>Be a part of Lantern on Hill lab! This training program will support your efforts to take your idea closer to implementation. As part of the project, aspiring entrepreneurs will receive a <strong>five-month support programme.</strong></p>
    <a class="btn" href="#">Read More</a>
  </div>
</section>

<section class="split why">
  <div class="split-copy">
    <h2>Why Lantern on Hill Lab?</h2>
    <p>Participants who successfully complete the programme will receive a certificate of participation. They will also be invited to dedicated exclusive monthly events and networking opportunities. Successful participants may also apply to participate in Lantern on Hill training's annual Investor Demo Day, which will be scheduled towards the end of 2020. Lantern on Hill training is offered free of charge as part of a research programme.</p>
  </div>
  <div class="split-media" role="img" aria-label="Wall illustration of an idea generator machine above wooden tables"></div>
</section>

<h2 class="section-title" style="top:2342px">FAQs</h2>
<div class="faq-list">
  <div class="faq-open">
    <div class="faq-q">What is the structure of training program?
      <svg class="chev" viewBox="0 0 14 14"><circle cx="7" cy="7" r="7" fill="var(--blue)"/><path d="M4,6 L7,9 L10,6" stroke="#fff" stroke-width="1.8" fill="none"/></svg></div>
    <p class="faq-a">The training will comprise of 8 sessions. Each session will be three-hour long and will be conducted in small groups with 1:25 facilitator-entrepreneur ratio.</p>
    <p class="faq-a">These sessions will be conducted on weekends during the months of April to August. They will be scheduled either on Saturday or Sunday</p>
  </div>
  <div class="faq-q">When and where is the Lantern on Hill training offered?<svg class="chev" viewBox="0 0 14 14"><circle cx="7" cy="7" r="7" fill="var(--blue)"/><path d="M6,4 L9,7 L6,10" stroke="#fff" stroke-width="1.8" fill="none"/></svg></div>
  <div class="faq-q">What is the fee for the training programme?<svg class="chev" viewBox="0 0 14 14"><circle cx="7" cy="7" r="7" fill="var(--blue)"/><path d="M6,4 L9,7 L6,10" stroke="#fff" stroke-width="1.8" fill="none"/></svg></div>
  <div class="faq-q">I do not live in Riverton, so how about travel and accommodation?<svg class="chev" viewBox="0 0 14 14"><circle cx="7" cy="7" r="7" fill="var(--blue)"/><path d="M6,4 L9,7 L6,10" stroke="#fff" stroke-width="1.8" fill="none"/></svg></div>
  <div class="faq-q">What is the content of training program?<svg class="chev" viewBox="0 0 14 14"><circle cx="7" cy="7" r="7" fill="var(--blue)"/><path d="M6,4 L9,7 L6,10" stroke="#fff" stroke-width="1.8" fill="none"/></svg></div>
  <div class="faq-q">Is it compulsory to attend all sessions?<svg class="chev" viewBox="0 0 14 14"><circle cx="7" cy="7" r="7" fill="var(--blue)"/><path d="M6,4 L9,7 L6,10" stroke="#fff" stroke-width="1.8" fill="none"/></svg></div>
  <div class="faq-q">Who are going to be the instructors/facilitators for the business support programme?<svg class="chev" viewBox="0 0 14 14"><circle cx="7" cy="7" r="7" fill="var(--blue)"/><path d="M6,4 L9,7 L6,10" stroke="#fff" stroke-width="1.8" fill="none"/></svg></div>
  <div class="faq-q">Who are eligible to join the programme?<svg class="chev" viewBox="0 0 14 14"><circle cx="7" cy="7" r="7" fill="var(--blue)"/><path d="M6,4 L9,7 L6,10" stroke="#fff" stroke-width="1.8" fill="none"/></svg></div>
</div>
<a class="faq-btn" href="#">View All FAQ</a>

<section class="split academic">
  <div class="split-media" role="img" aria-label="Bright desk with laptop, alarm clock, pencil and notebook"></div>
  <div class="split-copy">
    <h2>Academic Support</h2>
    <p>Northfield School of Business, in collaboration with Castellano University, will provide their world-renowned expertise in the field of management and entrepreneurship to deliver cutting-edge business knowledge to aspiring entrepreneurs with ideas in nascent phase..</p>
    <div class="partner-row">
      <div class="partner"><span class="partner-dot"></span>Northfield</div>
      <div class="partner"><span class="partner-dot"></span>Castellano University</div>
    </div>
  </div>
</section>

<section class="people">
  <h2>People</h2>
  <p class="people-lead">Links to Public profiles of the following people</p>
  <div class="card" style="left:76px"><div class="avatar" role="img" aria-label="Portrait photo"></div><h3>Arun Mehra</h3><p>Associate Professor of Strategy &amp; Entrepreneurship Northfield School of Business</p></div>
  <div class="card" style="left:344px"><div class="avatar" role="img" aria-label="Portrait photo"></div><h3>Priya Varma</h3><p>Assistant Professor of Entrepreneurship Northfield School of Business</p></div>
  <div class="card" style="left:612px"><div class="avatar" role="img" aria-label="Portrait photo"></div><h3>Marco Bellini</h3><p>Professor of Business Organization Castellano University</p></div>
  <div class="card" style="left:880px"><div class="avatar" role="img" aria-label="Portrait photo"></div><h3>Luca Ferranti</h3><p>Professor of Management Castellano University</p></div>
  <div class="dots"><span class="dot"></span><span class="dot on"></span></div>
</section>

<section class="apply">
  <div class="apply-photo" role="img" aria-label="Campus building exterior"></div>
  <svg class="people-wave" width="1200" height="110" viewBox="0 0 1200 110">
    <path d="M0,0 L1200,0 L1200,50 C850,110 400,60 0,20Z" fill="var(--blue)"/>
    <path d="M0,20 C400,60 850,110 1200,50 L1200,62 C850,124 400,74 0,32Z" fill="#ffffff"/>
  </svg>
  <h2>How to Apply</h2>
  <p class="apply-lead">If you are interested in applying, to hear from us,<br>Please provide following details and we will reach out to you with further information</p>
  <div class="field" style="left:252px;top:292px">Name:</div>
  <div class="field" style="left:612px;top:292px">Surname:</div>
  <div class="field" style="left:252px;top:354px">Email:</div>
  <div class="field" style="left:612px;top:354px">Phone:</div>
  <a class="btn" href="#">Submit</a>
</section>

<footer class="site-footer">
  <p class="copyright">Copyright © 2019. Company Name All Right Reserved</p>
  <div class="social" aria-label="Social links"><span></span><span></span><span></span><span></span><span></span><span class="x10">X10</span></div>
</footer>

</body>
</html>
```